Create a memorable Stationary for Security Software Company

Velbrantix is the worldwide leader in securing the Internet. Making Internet communications and critical data secure, reliable and available everywhere has been and continues to be our ongoing vision. We are committed to staying focused on real customer needs and to developing new and innovative security solutions that redefine the security landscape.

Industry/Entity Type

Internet

Font styles to use
Serif
Sans Serif
Script

Colors
0792cd
33a6d7
85cae6

```html
<!DOCTYPE html>
<html lang="en">
<head>
<meta charset="utf-8">
<title>Velbrantix Business Card</title>
<link href="https://fonts.googleapis.com/css2?family=Open+Sans:wght@400;600;700&display=swap" rel="stylesheet">
<style>
  :root {
    --blue-deep: #0792cd;
    --blue-mid: #33a6d7;
    --blue-light: #85cae6;
    --paper: #ffffff;
    --ink: #3a3a3a;
    --backdrop: #ecebe8;
  }
  * { margin: 0; padding: 0; box-sizing: border-box; }
  html, body {
    width: 1200px; height: 1120px; overflow: hidden;
    background: var(--backdrop);
    font-family: "Open Sans", sans-serif;
  }
  .sheet {
    width: 1200px; height: 1120px;
    display: flex; flex-direction: column; align-items: center; justify-content: center;
    gap: 60px;
  }
  .card {
    position: relative;
    width: 840px; height: 480px;
    overflow: hidden;
    box-shadow: 0 6px 18px rgba(0,0,0,0.18);
  }
  .card-front { background: var(--paper); }
  .brand {
    display: flex; align-items: center; gap: 14px;
    color: var(--blue-mid);
    font-weight: 700;
    letter-spacing: 0.5px;
  }
  .brand-dot {
    width: 34px; height: 34px; border-radius: 50%;
    background: var(--blue-mid);
  }
  .card-front .brand {
    position: absolute; left: 0; right: 0; top: 150px;
    justify-content: center; font-size: 62px;
  }
  .card-front .brand-dot { width: 46px; height: 46px; }
  .front-url {
    position: absolute; left: 0; right: 0; top: 330px;
    text-align: center;
    color: var(--ink);
    font-size: 24px; letter-spacing: 5px;
  }
  .card-back { background: var(--blue-light); }
  .back-cloud { position: absolute; inset: 0; }
  .card-back .brand {
    position: absolute; left: 70px; top: 205px;
    font-size: 48px;
  }
  .contact {
    position: absolute; right: 70px; top: 52px;
    text-align: right; color: var(--paper);
  }
  .contact-name { font-size: 30px; font-weight: 700; line-height: 1.15; }
  .contact-title { font-size: 22px; margin-bottom: 40px; }
  .contact-list { list-style: none; font-size: 20px; line-height: 1.7; }
  .contact-list li { display: flex; justify-content: flex-end; align-items: center; gap: 10px; }
  .contact-list svg { width: 18px; height: 18px; flex: none; }
  .contact-list .address { align-items: flex-start; margin-top: 6px; line-height: 1.3; }
  .contact-list .address svg { width: 22px; height: 22px; margin-top: 2px; }
</style>
</head>
<body>
<main class="sheet">
  <section class="card card-front">
    <div class="brand"><span class="brand-dot"></span>Velbrantix</div>
    <p class="front-url">www.velbrantix.com</p>
  </section>

  <section class="card card-back">
    <svg class="back-cloud" viewBox="0 0 840 480" aria-hidden="true">
      <path fill="var(--blue-mid)" transform="translate(-12 0)" d="M852 0 H610 C565 0 545 40 565 72 C520 84 512 140 548 168 C470 180 452 262 494 302 C444 334 446 422 506 444 C526 472 566 480 610 480 H852 Z"/>
      <path fill="var(--blue-deep)" d="M852 0 H610 C565 0 545 40 565 72 C520 84 512 140 548 168 C470 180 452 262 494 302 C444 334 446 422 506 444 C526 472 566 480 610 480 H852 Z"/>
    </svg>
    <div class="brand"><span class="brand-dot"></span>Velbrantix</div>
    <div class="contact">
      <p class="contact-name">Your Name</p>
      <p class="contact-title">Title</p>
      <ul class="contact-list">
        <li>
          <svg viewBox="0 0 20 20"><circle cx="10" cy="10" r="8" fill="none" stroke="#fff" stroke-width="2"/><path d="M7 6 q-1 5 5 8 l1.5-1.5 -2-2 -1 1 q-2-1-2.5-3 l1-1 -1-2.5z" fill="#fff"/></svg>
          012-345-6789
        </li>
        <li>
          <svg viewBox="0 0 20 20"><rect x="5" y="1" width="10" height="18" rx="2" fill="#fff"/><rect x="7" y="4" width="6" height="8" fill="var(--blue-deep)"/></svg>
          012-345-6789
        </li>
        <li>
          <svg viewBox="0 0 20 20"><rect x="1" y="4" width="18" height="12" rx="2" fill="#fff"/><path d="M2 5 l8 6 8-6" fill="none" stroke="var(--blue-deep)" stroke-width="1.6"/></svg>
          info@velbrantix.com
        </li>
        <li>
          <svg viewBox="0 0 20 20" fill="none" stroke="#fff" stroke-width="1.6"><circle cx="10" cy="10" r="8"/><ellipse cx="10" cy="10" rx="3.5" ry="8"/><path d="M2 10 h16 M3.5 6 h13 M3.5 14 h13"/></svg>
          www.velbrantix.com
        </li>
        <li class="address">
          <svg viewBox="0 0 20 20"><circle cx="10" cy="10" r="9" fill="#fff"/><path d="M10 4 a3.5 3.5 0 0 1 3.5 3.5 c0 2.5-3.5 7-3.5 7 s-3.5-4.5-3.5-7 A3.5 3.5 0 0 1 10 4z" fill="var(--blue-deep)"/><circle cx="10" cy="7.5" r="1.3" fill="#fff"/></svg>
          <span>Street Name, City Name<br>Zipcode-012345</span>
        </li>
      </ul>
    </div>
  </section>
</main>
</body>
</html>
```